PROPERTY MANAGEMENT AND REAL ESTATE

Target Market(s)

real estate owners and investors

Industry/Entity Type

Real Estate

Contact Information for Business Card

BRIGHT LANTERN PROPERTY MANAGEMENT GROUP, LLC
287 North Willowmere Parkway
Suite 240
Hallandale Beach, FL 33071

```html
<!DOCTYPE html>
<html lang="en">
<head>
<meta charset="utf-8">
<title>Bright Lantern Property Management Group – Business Card</title>
<link rel="stylesheet" href="https://fonts.googleapis.com/css2?family=Montserrat:wght@400;500;600&family=Exo+2:wght@400;500&display=swap">
<style>
  :root {
    --backdrop: #3b3b3d;
    --card: #ffffff;
    --band: #0b0b0b;
    --accent: #8e0f0f;
    --ink: #1e1e1e;
    --rule: #7a7a7a;
    --on-band: #ffffff;
  }
  * { box-sizing: border-box; margin: 0; padding: 0; }
  html, body {
    width: 1200px; height: 817px; overflow: hidden;
    background: var(--backdrop);
  }
  .canvas {
    position: relative; width: 1200px; height: 817px;
    display: flex; align-items: center; justify-content: center;
  }
  .card {
    position: relative; width: 960px; height: 560px;
    background: var(--card); border-radius: 30px; overflow: hidden;
    font-family: "Montserrat", sans-serif; color: var(--ink);
  }
  .brand {
    position: absolute; left: 56px; top: 60px;
    display: flex; align-items: center; gap: 18px;
  }
  .brand-dot {
    width: 78px; height: 78px; border-radius: 50%; background: var(--accent);
  }
  .brand-name {
    font-family: "Montserrat", sans-serif; font-weight: 400;
    font-size: 19px; line-height: 1.25; letter-spacing: 0.3px;
    text-transform: uppercase; color: var(--ink);
  }
  .name-band {
    position: absolute; left: 0; right: 0; top: 178px; height: 56px;
    background: var(--band); color: var(--on-band);
    display: flex; align-items: center; padding-left: 40px;
  }
  .name-band .person-icon { width: 34px; height: 40px; margin-right: 18px; }
  .person-name {
    font-weight: 500; font-size: 28px; letter-spacing: 1px; text-transform: uppercase;
  }
  .divider {
    width: 2px; height: 26px; background: var(--on-band); margin: 0 18px;
  }
  .person-title {
    font-weight: 500; font-size: 18px; letter-spacing: 1.2px; text-transform: uppercase;
  }
  .contacts {
    position: absolute; left: 0; right: 0; top: 234px; height: 240px;
    display: grid; grid-template-columns: 1fr 1fr 1fr;
  }
  .contact {
    position: relative; display: flex; flex-direction: column;
    align-items: center; justify-content: center; gap: 26px;
    padding: 0 24px; min-width: 0;
  }
  .contact + .contact::before {
    content: ""; position: absolute; left: 0; top: 28px; bottom: 38px;
    width: 3px; background: var(--rule);
  }
  .icon-disc {
    width: 76px; height: 76px; border-radius: 50%; background: var(--accent);
    display: flex; align-items: center; justify-content: center;
  }
  .icon-disc svg { width: 40px; height: 40px; }
  .contact-text {
    font-family: "Exo 2", sans-serif; font-size: 23px; letter-spacing: 0.8px;
    color: var(--ink); white-space: nowrap;
  }
  .contact-text.phone { font-size: 28px; letter-spacing: 3px; }
  .address-band {
    position: absolute; left: 0; right: 0; bottom: 36px; height: 50px;
    background: var(--band); color: var(--on-band);
    display: flex; align-items: center; padding-left: 40px; gap: 16px;
  }
  .address-band svg { width: 22px; height: 30px; }
  .address {
    font-family: "Exo 2", sans-serif; font-size: 19px; letter-spacing: 2.2px;
    white-space: nowrap;
  }
</style>
</head>
<body>
<main class="canvas">
  <section class="card" aria-label="Business card">
    <header class="brand">
      <span class="brand-dot" aria-hidden="true"></span>
      <p class="brand-name">Bright Lantern Property<br>Management Group, LLC</p>
    </header>

    <div class="name-band">
      <svg class="person-icon" viewBox="0 0 34 40" aria-hidden="true">
        <circle cx="17" cy="11" r="9" fill="#fff"/>
        <path d="M1 40 C1 27 8 22 17 22 C26 22 33 27 33 40 Z" fill="#fff"/>
      </svg>
      <span class="person-name">Daniel Mercer</span>
      <span class="divider" aria-hidden="true"></span>
      <span class="person-title">General Manager</span>
    </div>

    <div class="contacts">
      <div class="contact">
        <span class="icon-disc">
          <svg viewBox="0 0 40 40" aria-hidden="true">
            <rect x="11" y="3" width="18" height="34" rx="3" fill="none" stroke="#fff" stroke-width="2.5"/>
            <line x1="11" y1="9" x2="29" y2="9" stroke="#fff" stroke-width="2"/>
            <line x1="11" y1="30" x2="29" y2="30" stroke="#fff" stroke-width="2"/>
            <circle cx="20" cy="33.5" r="1.6" fill="#fff"/>
          </svg>
        </span>
        <span class="contact-text phone">012 555 0148</span>
      </div>
      <div class="contact">
        <span class="icon-disc">
          <svg viewBox="0 0 40 40" aria-hidden="true">
            <rect x="4" y="9" width="32" height="22" fill="#fff"/>
            <path d="M4 9 L20 22 L36 9" fill="none" stroke="#8e0f0f" stroke-width="2"/>
            <path d="M4 31 L16 19 M36 31 L24 19" fill="none" stroke="#8e0f0f" stroke-width="1.5"/>
          </svg>
        </span>
        <span class="contact-text">dmercer@blpmgroup.com</span>
      </div>
      <div class="contact">
        <span class="icon-disc">
          <svg viewBox="0 0 40 40" aria-hidden="true">
            <g fill="none" stroke="#fff" stroke-width="2">
              <circle cx="20" cy="20" r="15"/>
              <ellipse cx="20" cy="20" rx="7" ry="15"/>
              <line x1="20" y1="5" x2="20" y2="35"/>
              <line x1="5" y1="20" x2="35" y2="20"/>
              <path d="M8 12 H32 M8 28 H32"/>
            </g>
          </svg>
        </span>
        <span class="contact-text">www.blpmgroup.com</span>
      </div>
    </div>

    <footer class="address-band">
      <svg viewBox="0 0 22 30" aria-hidden="true">
        <path d="M11 1 C5 1 1 5.5 1 11 C1 18 11 29 11 29 C11 29 21 18 21 11 C21 5.5 17 1 11 1 Z" fill="#fff"/>
        <circle cx="11" cy="11" r="4" fill="#0b0b0b"/>
      </svg>
      <span class="address">287 North Willowmere Parkway, Suite 240, Hallandale Beach, FL 33071</span>
    </footer>
  </section>
</main>
</body>
</html>
```